Webshop for furniture and lamps

We need a design for a web shop with APP that should have two options:
1-Webshop in general which should attract to private customer in general and
2-Website that is meant to attract big customers as hotels and restaurants who would have their own customerize login.

That's the idea behind the shop.

It should be diveded into 4 parts
vintage furniture
rattan set outdoor and indoor
lamps and
wooden wall decor

The name of the shop is loma vereda!

Please kindly make me an offer.

Reason: Dear designers, so far there hasn't been a design that really matched. Look up German web sites like www.glimmerhof-wohnen.de or www.sitzraum77.de... Haven't been convinced by designs! Sorry folks. Please submit some new ones. Kind regards Ned

```html
<!DOCTYPE html>
<html lang="en">
<head>
<meta charset="utf-8">
<title>loma vereda – Welcome</title>
<link href="https://fonts.googleapis.com/css2?family=Open+Sans:wght@400;700&display=swap" rel="stylesheet">
<style>
  :root {
    --text-light: #ffffff;
    --accent-orange: #f28a1a;
    --scene-top: #4a4c58;
    --scene-mid: #35302d;
    --scene-deep: #221b17;
    --scene-edge: #15110e;
  }
  html, body {
    margin: 0;
    padding: 0;
    width: 1200px;
    height: 581px;
    overflow: hidden;
    background: var(--scene-edge);
  }
  .welcome-hero {
    position: relative;
    width: 1200px;
    height: 581px;
    overflow: hidden;
    font-family: "Open Sans", Arial, sans-serif;
    color: var(--text-light);
  }
  .hero-backdrop {
    position: absolute;
    inset: 0;
    background:
      radial-gradient(ellipse 70% 55% at 55% 70%, rgba(70, 56, 44, 0.55), transparent 70%),
      linear-gradient(180deg, var(--scene-top) 0%, var(--scene-mid) 38%, var(--scene-deep) 72%, var(--scene-edge) 100%);
  }
  .hero-title {
    position: absolute;
    top: 126px;
    left: 0;
    width: 100%;
    margin: 0;
    text-align: center;
    font-weight: 700;
    font-size: 72px;
    line-height: 96px;
    letter-spacing: 1px;
  }
  .hero-intro {
    position: absolute;
    top: 280px;
    left: 0;
    width: 100%;
    margin: 0;
    text-align: center;
    font-weight: 400;
    font-size: 19.5px;
    line-height: 32px;
  }
  .membership-line {
    position: absolute;
    top: 424px;
    left: 0;
    width: 100%;
    margin: 0;
    text-align: center;
    font-size: 19.5px;
    line-height: 32px;
  }
  .action-link {
    color: var(--accent-orange);
    font-weight: 700;
    text-decoration: none;
  }
  .terms-link {
    position: absolute;
    top: 507px;
    left: 0;
    width: 100%;
    text-align: center;
    font-size: 14.5px;
    line-height: 22px;
    color: var(--text-light);
    text-decoration: none;
  }
</style>
</head>
<body>
  <main class="welcome-hero">
    <div class="hero-backdrop" role="img" aria-label="Dim living room photograph: a distressed dark wooden chest used as coffee table with an open magazine and glass candle holders, a light sofa with cushions behind"></div>

    <h1 class="hero-title">WELCOME VISITORS</h1>

    <p class="hero-intro">
      Join us and get our special promo every week<br>
      for New Member please <a class="action-link" href="#">SIGN UP</a> here
    </p>

    <p class="membership-line">
      Business Membership <a class="action-link" href="#">SIGN IN</a> here and Private Customer Membership <a class="action-link" href="#">SIGN IN</a> here
    </p>

    <a class="terms-link" href="#">terms and conditions</a>
  </main>
</body>
</html>
```